Boutique Store Selling Antiques and Unique Finds

I need a Web Page designed for my Store Called "Willow Lane". I would like a very classic, muted design that looks European when pulled up. I will be selling Antiques from all over the world and Unique finds that have reproduced. I will also be selling high-end purses and jewelry with unique, reasonable products for the every-day buyer as well.

Target Market(s)

25-70 year old men and women;)

Coding

Coded - Design and coding required

Number of Pages Required

1 page

Colors

Designer to choose only greyscale colors for use in the design.

Requirements
Must have
• I want it

```html
<!DOCTYPE html>
<html lang="en">
<head>
<meta charset="utf-8">
<title>Willow Lane — Antiques and Unique Finds</title>
<link rel="stylesheet" href="https://fonts.googleapis.com/css2?family=Roboto+Slab:wght@300;400;700;800&family=Zilla+Slab:wght@300;400;600;700&display=block">
<style>
  :root {
    --cream: #f8f1e3;
    --ink: #2b2623;
    --ink-soft: #4a4440;
    --accent: #e0762a;
    --heading-brown: #b07a45;
    --line: #c9bfae;
    --white: #ffffff;
    --slab: "Roboto Slab", "Zilla Slab", Rockwell, "Rockwell Extra Bold", serif;
    --text: "Zilla Slab", "Roboto Slab", Rockwell, serif;
  }
  * { box-sizing: border-box; margin: 0; padding: 0; }
  html, body { width: 826px; height: 1200px; overflow: hidden; }
  body {
    position: relative;
    background: var(--cream);
    font-family: var(--text);
    color: var(--ink);
  }
  .abs { position: absolute; }

  /* Hero */
  .hero {
    position: absolute; left: 0; top: 0; width: 826px; height: 404px;
    background:
      radial-gradient(circle at 95px 115px, rgba(222,146,78,.75) 0 48px, rgba(222,146,78,0) 62px),
      radial-gradient(circle at 205px 50px, rgba(215,140,72,.55) 0 55px, rgba(215,140,72,0) 75px),
      radial-gradient(circle at 255px 85px, rgba(225,150,82,.6) 0 40px, rgba(225,150,82,0) 52px),
      radial-gradient(circle at 220px 195px, rgba(215,140,75,.7) 0 22px, rgba(215,140,75,0) 28px),
      radial-gradient(circle at 152px 335px, rgba(205,150,95,.55) 0 48px, rgba(205,150,95,0) 62px),
      radial-gradient(ellipse 70px 240px at 720px 170px, rgba(55,30,55,.7) 0, rgba(55,30,55,0) 100%),
      radial-gradient(ellipse 200px 70px at 600px 180px, rgba(210,175,140,.45) 0, rgba(210,175,140,0) 100%),
      linear-gradient(180deg, #9a6a42 0%, #7e5238 30%, #5a3a3a 55%, #3a2533 80%, #2c1e2a 100%);
  }
  .menu-icon { left: 168px; top: 29px; width: 16px; height: 12px; }
  .site-name {
    left: 0; width: 826px; top: 45px; text-align: center;
    color: var(--white); font-family: var(--slab); font-size: 15px; font-weight: 400;
    letter-spacing: 3.5px; text-transform: uppercase;
  }
  .fav-icon { left: 594px; top: 28px; width: 15px; height: 14px; }
  .cart-icon { left: 627px; top: 29px; width: 14px; height: 14px; }
  .cart-count { left: 644px; top: 27px; color: var(--white); font-size: 11px; font-family: Arial, sans-serif; }
  .hero-title {
    left: 0; width: 826px; top: 205px; text-align: center;
    color: var(--white); font-family: var(--slab); font-size: 41px; font-weight: 800;
    line-height: 50px; letter-spacing: .5px;
  }
  .hero-tagline {
    left: 0; width: 826px; top: 259px; text-align: center;
    color: var(--white); font-family: var(--slab); font-size: 16.5px; font-weight: 300;
  }
  .btn-shop {
    left: 350px; top: 304px; width: 126px; height: 28px;
    border: 2px solid var(--accent); color: var(--white);
    font-family: var(--slab); font-size: 14px; font-weight: 700; text-align: center; line-height: 24px;
  }
  .scroll-down {
    left: 389px; top: 382px; width: 48px; height: 48px; border-radius: 50%;
    background: var(--cream);
  }
  .scroll-down svg { position: absolute; left: 18px; top: 17px; }

  /* Shop */
  .section-title {
    left: 0; width: 826px; top: 480px; text-align: center;
    color: var(--heading-brown); font-family: var(--slab); font-size: 20px; font-weight: 800; letter-spacing: .5px;
  }
  .product-grid {
    left: 168px; top: 525px; width: 490px; height: 256px;
    border: 1px solid var(--line);
  }
  .product-grid .divider { left: 244px; top: 0; width: 1px; height: 254px; background: var(--line); }
  .product-photo { top: 8px; width: 233px; height: 200px; }
  .product-photo.crown-gold {
    left: 6px;
    background:
      radial-gradient(ellipse 105px 60px at 116px 105px, rgba(160,120,50,.95) 0, rgba(140,100,45,.7) 60%, rgba(140,100,45,0) 100%),
      radial-gradient(ellipse 90px 25px at 116px 60px, rgba(170,130,60,.7) 0, rgba(170,130,60,0) 100%),
      linear-gradient(180deg, #cbc5bd 0%, #bdb6ac 45%, #3a3328 58%, #6e4a26 70%, #8a5a2c 88%, #5a2a22 100%);
  }
  .product-photo.crown-french {
    left: 250px;
    background:
      radial-gradient(ellipse 80px 65px at 116px 115px, rgba(130,95,60,.95) 0, rgba(120,85,55,.7) 60%, rgba(120,85,55,0) 100%),
      radial-gradient(ellipse 40px 30px at 116px 185px, rgba(45,45,45,.95) 0, rgba(45,45,45,0) 100%),
      linear-gradient(180deg, #6b5227 0%, #a07a3a 7%, #2a2622 12%, #2a2622 20%, #8a7048 24%, #e8e4dc 30%, #dedad2 70%, #3a3634 88%, #1e1c1b 100%);
  }
  .product-name, .product-price {
    width: 233px; text-align: center; font-size: 7.5px; color: var(--ink-soft);
  }
  .product-name { top: 219px; }
  .product-price { top: 231px; }
  .col-a { left: 6px; }
  .col-b { left: 250px; }
  .pager { left: 387px; top: 808px; width: 52px; height: 8px; }

  /* Newsletter */
  .newsletter {
    left: 169px; top: 846px; width: 486px; height: 163px;
    background:
      radial-gradient(ellipse 60px 30px at 140px 60px, rgba(150,70,50,.35) 0, rgba(150,70,50,0) 100%),
      radial-gradient(ellipse 70px 40px at 300px 125px, rgba(140,60,50,.3) 0, rgba(140,60,50,0) 100%),
      linear-gradient(155deg, #4a403a 0%, #3a322d 30%, #2a2420 60%, #1a1614 100%);
  }
  .newsletter-title {
    left: 0; width: 486px; top: 30px; text-align: center;
    color: var(--white); font-family: var(--slab); font-size: 20px; font-weight: 800;
  }
  .newsletter-text {
    left: 0; width: 486px; top: 63px; text-align: center;
    color: var(--white); font-family: var(--slab); font-size: 10px; font-weight: 400; letter-spacing: .2px;
  }
  .email-field {
    left: 72px; top: 92px; width: 218px; height: 28px;
    border: 2px solid var(--accent); color: var(--white);
    font-family: var(--slab); font-size: 9px; line-height: 24px; padding-left: 13px;
  }
  .btn-subscribe {
    left: 289px; top: 92px; width: 127px; height: 28px;
    border: 2px solid var(--accent); color: var(--white);
    font-family: var(--slab); font-size: 14px; font-weight: 800; text-align: center; line-height: 24px;
  }

  /* Footer */
  .footer-box {
    left: 169px; top: 1027px; width: 486px; height: 135px;
    border: 1px solid var(--line);
  }
  .footer-box .divider { top: 0; width: 1px; height: 133px; background: var(--line); }
  .footer-heading { top: 16px; font-family: var(--slab); font-size: 9.5px; font-weight: 700; color: var(--ink); }
  .footer-text { top: 44px; font-size: 6.6px; line-height: 10.4px; color: var(--ink); }
  .footer-brand {
    left: 18px; top: 111px; font-family: var(--slab); font-size: 8.5px; letter-spacing: 2px;
    text-transform: uppercase; color: var(--ink);
  }
  .copyright {
    left: 0; width: 826px; top: 1178px; text-align: center; font-size: 6.8px; color: var(--ink);
  }
  .page-mark { left: 647px; top: 1180px; font-size: 6.5px; color: var(--ink); }
</style>
</head>
<body>
  <header class="hero" role="img" aria-label="Photo of an ornate jewelled crown resting on a sword in dusky grass with warm bokeh lights"></header>

  <svg class="abs menu-icon" viewBox="0 0 16 12" aria-label="Menu">
    <rect y="0" width="16" height="2" fill="#fff"/>
    <rect y="5" width="16" height="2" fill="#fff"/>
    <rect y="10" width="16" height="2" fill="#fff"/>
  </svg>
  <div class="abs site-name">Willow Lane</div>
  <svg class="abs fav-icon" viewBox="0 0 24 22" aria-label="Favourites">
    <path d="M12 20 L3 11 C0 8 1 3 5.5 2.5 C8.5 2.2 10.5 4 12 6 C13.5 4 15.5 2.2 18.5 2.5 C23 3 24 8 21 11 Z" fill="none" stroke="#fff" stroke-width="1.6"/>
  </svg>
  <svg class="abs cart-icon" viewBox="0 0 24 24" aria-label="Cart">
    <path d="M1 3 H5 L8 15 H20 L22 6 H6" fill="none" stroke="#fff" stroke-width="1.6"/>
    <circle cx="9" cy="20" r="1.8" fill="none" stroke="#fff" stroke-width="1.4"/>
    <circle cx="18" cy="20" r="1.8" fill="none" stroke="#fff" stroke-width="1.4"/>
  </svg>
  <div class="abs cart-count">(0)</div>

  <h1 class="abs hero-title">WILLOW LANE</h1>
  <p class="abs hero-tagline">We are a Boutique Store Selling Antiques and Unique Finds.</p>
  <div class="abs btn-shop">Shop Now</div>

  <div class="abs scroll-down">
    <svg width="12" height="8" viewBox="0 0 12 8"><path d="M1 1 L6 6 L11 1" fill="none" stroke="#e0762a" stroke-width="1.6"/></svg>
  </div>

  <h2 class="abs section-title">OUR SHOP</h2>

  <section class="abs product-grid">
    <div class="abs divider"></div>
    <div class="abs product-photo crown-gold" role="img" aria-label="Photo of a large gilded star crown set on an old leather book"></div>
    <div class="abs product-name col-a">Large crown</div>
    <div class="abs product-price col-a">$56.00</div>
    <div class="abs product-photo crown-french" role="img" aria-label="Photo of a French jewelled crown on a dark stand before a gilt frame"></div>
    <div class="abs product-name col-b">French crown</div>
    <div class="abs product-price col-b">$56.00</div>
  </section>

  <svg class="abs pager" viewBox="0 0 52 8" aria-label="Slide indicator">
    <circle cx="6" cy="4" r="3" fill="#2b2623"/>
    <circle cx="19" cy="4" r="2.6" fill="none" stroke="#2b2623" stroke-width=".8"/>
    <circle cx="33" cy="4" r="3" fill="#2b2623"/>
    <circle cx="46" cy="4" r="3" fill="#2b2623"/>
  </svg>

  <section class="abs newsletter" role="img" aria-label="Dark close-up photo of a jewelled antique crown with pearls and gems">
    <h2 class="abs newsletter-title">JOIN EMAIL</h2>
    <p class="abs newsletter-text">Sign up to receive the latest news and updates</p>
    <div class="abs email-field">Enter email</div>
    <div class="abs btn-subscribe">Subscribe</div>
  </section>

  <footer class="abs footer-box">
    <div class="abs divider" style="left:162px"></div>
    <div class="abs divider" style="left:324px"></div>

    <h3 class="abs footer-heading" style="left:19px">ABOUT</h3>
    <p class="abs footer-text" style="left:18px;width:135px">Neque porro quisquam est, qui dolorem ipsum quia dolor sit amet, consectetur, adipisci velit, sed quia non numquam eius modi tempora incidunt ut labore et dolore magnam aliquam quaerat voluptatem.</p>
    <div class="abs footer-brand">Willow Lane</div>

    <h3 class="abs footer-heading" style="left:180px">TERMS AND CONDITIONS</h3>
    <p class="abs footer-text" style="left:179px">Terms and Conditions<br>Privacy Policy<br>GDPR</p>

    <h3 class="abs footer-heading" style="left:338px">SOCIAL</h3>
    <p class="abs footer-text" style="left:337px">Photogram<br>Friendbook<br>Pinboard<br>Chirper</p>
  </footer>

  <div class="abs copyright">2021 © www.willowlanestore.com</div>
  <div class="abs page-mark">M1</div>
</body>
</html>
```